Cover für ein Ebook mit dem Thema Akne
Zielgruppe
Design für 80 % Junge Leute, sollte positives ausstrahlen und auch in Verbindung mit en bestimmten Farben wie Helltürkis oä. modern und profesionell wirken. Es handelt sich um das Thema Akne aber auch ein großer Teil Ernährung und um die Psyche geht es ebenfalls.
es sollte etwas herausstechen durch Farben aber auch sehr modern wirken.
Aufgabenstellung
Es sollte die Aufmerksamkeit wecken und ein positives Gefühl vermitteln und nicht nur mit Grau weiss Schwarz 'trostlos' wirken. Es sollte etwas herausstechen. Titel des Buches :
Klare Tage- Haut begreifen und meistern.
Es sollte neugierig machen und das Cover sollte 'Hoffnung, positives und fröhliches spiegeln
gerne auch mit Farben, 2 maximal 3 'Bunte Farben' Grau, Schwarz und Weiss zähle ich nicht zu diesen Bunten Farben. Das Cover und vorallem die Schrift sollten auch bei keiner Vergrößerung also bei kleiner Darstellung auf einnem E- Reader lesbar und erkennbar sein.
Es sollte aber auch für Schwarz- Weiss Reader die keine Farben anzeigen, attraktiv aussehen.
Auf dem Cover sollte der Name sein : Lukas Stein
Und der Titel : Klare Tage- Haut begreifen und meistern

```html
<!DOCTYPE html>
<html lang="de">
<head>
<meta charset="utf-8">
<title>Klare Tage – Haut begreifen und meistern · Cover-Varianten</title>
<link rel="stylesheet" href="https://fonts.googleapis.com/css2?family=Amatic+SC:wght@700&family=Patrick+Hand+SC&family=Open+Sans:wght@400&display=swap">
<style>
  :root {
    --page: #ffffff;
    --frame: #5a5a5a;
    --ink: #1a1a1a;
    --tag-bg: #111111;
    --tag-text: #ffffff;
    --green: #55b373;
    --teal: #86c0b0;
    --grey-dark: #808080;
    --grey-light: #9b9b9b;
    --paper: #ffffff;
    --title-light: #ffffff;
    --green-ink: #2f9c52;
    --teal-ink: #7cc3a7;
  }
  * { box-sizing: border-box; margin: 0; padding: 0; }
  html, body {
    width: 1200px; height: 639px; overflow: hidden;
    background: var(--page);
  }
  .sheet { position: relative; width: 1200px; height: 639px; }
  .cover {
    position: absolute; top: 27px;
    width: 362px; height: 587px;
    border: 1px solid var(--frame);
    overflow: hidden;
  }
  .cover--color { left: 27px; }
  .cover--grey  { left: 419px; }
  .cover--white { left: 811px; background: var(--paper); }
  .cover__bg { position: absolute; inset: 0; width: 100%; height: 100%; }
  .cover__tag {
    position: absolute; top: 0; right: 0;
    width: 96px; height: 32px;
    background: var(--tag-bg); color: var(--tag-text);
    font: 400 13px/32px "Open Sans", sans-serif;
    text-align: center;
  }
  .cover__title {
    position: absolute; inset: 0;
    font-family: "Amatic SC", cursive;
    font-weight: 700;
    color: var(--title-light);
    text-transform: uppercase;
  }
  .cover__title-top {
    position: absolute; left: 24px; top: 30px;
    font-size: 120px; line-height: 1;
    transform: rotate(-4deg);
  }
  .cover__title-main {
    position: absolute; left: 0; right: 0; top: 130px;
    text-align: center;
    font-size: 232px; line-height: 1;
    letter-spacing: 4px;
    transform: rotate(-4deg);
  }
  .cover--white .cover__title-top { color: var(--teal-ink); }
  .cover--white .cover__title-main { color: var(--green-ink); }
  .cover__author {
    position: absolute; left: 172px; top: 112px;
    width: 180px; text-align: center;
    font: 400 27px/1 "Patrick Hand SC", cursive;
    text-transform: uppercase;
    transform: rotate(-10deg);
    color: var(--ink);
  }
  .cover__mascot { position: absolute; left: 132px; top: 358px; width: 128px; height: 118px; }
  .cover__subtitle {
    position: absolute; left: 0; right: 0; top: 490px;
    text-align: center;
    font: 400 28px/34px "Patrick Hand SC", cursive;
    text-transform: uppercase;
    color: var(--ink);
    letter-spacing: 0.5px;
  }
</style>
</head>
<body>
<main class="sheet">

  <section class="cover cover--color" aria-label="Farbvariante">
    <svg class="cover__bg" viewBox="0 0 362 587" aria-hidden="true">
      <rect width="362" height="587" fill="var(--teal)"/>
      <polygon points="0,0 362,0 362,319 0,380" fill="var(--green)"/>
    </svg>
    <h1 class="cover__title">
      <span class="cover__title-top">Klare</span>
      <span class="cover__title-main">Tage</span>
    </h1>
    <div class="cover__tag">Ratgeber</div>
    <p class="cover__author">Lukas Stein</p>
    <svg class="cover__mascot" viewBox="0 0 128 118" role="img" aria-label="Illustration: fröhliches Krokodil als Maskottchen">
      <rect width="128" height="118" rx="14" fill="#6a9a8c"/>
    </svg>
    <p class="cover__subtitle">Haut begreifen<br>und meistern</p>
  </section>

  <section class="cover cover--grey" aria-label="Graustufenvariante">
    <svg class="cover__bg" viewBox="0 0 362 587" aria-hidden="true">
      <rect width="362" height="587" fill="var(--grey-light)"/>
      <polygon points="0,0 362,0 362,319 0,380" fill="var(--grey-dark)"/>
    </svg>
    <h2 class="cover__title">
      <span class="cover__title-top">Klare</span>
      <span class="cover__title-main">Tage</span>
    </h2>
    <div class="cover__tag">Ratgeber</div>
    <p class="cover__author">Lukas Stein</p>
    <svg class="cover__mascot" viewBox="0 0 128 118" role="img" aria-label="Illustration: fröhliches Krokodil als Maskottchen">
      <rect width="128" height="118" rx="14" fill="#6e6e6e"/>
    </svg>
    <p class="cover__subtitle">Haut begreifen<br>und meistern</p>
  </section>

  <section class="cover cover--white" aria-label="Variante auf Weiß">
    <h2 class="cover__title">
      <span class="cover__title-top">Klare</span>
      <span class="cover__title-main">Tage</span>
    </h2>
    <div class="cover__tag">Ratgeber</div>
    <p class="cover__author">Lukas Stein</p>
    <svg class="cover__mascot" viewBox="0 0 128 118" role="img" aria-label="Illustration: fröhliches Krokodil als Maskottchen">
      <rect width="128" height="118" rx="14" fill="var(--teal-ink)" fill-opacity="0.6"/>
    </svg>
    <p class="cover__subtitle">Haut begreifen<br>und meistern</p>
  </section>

</main>
</body>
</html>
```